Construction business card

I need a new business card, they can connect with my logo, brand.
What we do is residential house , design and build
I like: Navy blue / black
I attached our logo, brand,
and, some idea for business card.

```html
<!DOCTYPE html>
<html lang="en">
<head>
<meta charset="utf-8">
<title>Ridgeline Building Group – Business Card</title>
<link href="https://fonts.googleapis.com/css2?family=Lato:wght@400;700&display=swap" rel="stylesheet">
<style>
  :root {
    --backdrop: #1f1f1f;
    --card-blue: #0281ec;
    --card-ink: #ffffff;
    --emboss: #0a6fcf;
    --emboss-light: #2a90f0;
  }
  * { box-sizing: border-box; margin: 0; padding: 0; }
  html, body {
    width: 1200px;
    height: 897px;
    overflow: hidden;
    background: var(--backdrop);
    font-family: "Lato", sans-serif;
  }
  .canvas {
    position: relative;
    width: 1200px;
    height: 897px;
  }
  .card {
    position: absolute;
    left: 258px;
    width: 684px;
    height: 380px;
    background: var(--card-blue);
    color: var(--card-ink);
    box-shadow: 0 10px 24px rgba(0,0,0,0.55);
  }
  .card--front { top: 48px; }
  .card--back { top: 470px; }

  .front-brand {
    position: absolute;
    inset: 0;
    display: flex;
    align-items: center;
    justify-content: center;
  }
  .brand-name {
    font-weight: 700;
    font-size: 40px;
    letter-spacing: 3px;
    text-transform: uppercase;
    color: var(--card-ink);
    text-align: center;
    line-height: 1.15;
  }

  .holder {
    position: absolute;
    left: 44px;
    top: 52px;
  }
  .holder-name {
    font-size: 30px;
    font-weight: 400;
    letter-spacing: 2px;
    text-transform: uppercase;
  }
  .holder-role {
    font-size: 16px;
    margin-top: 4px;
    letter-spacing: 0.5px;
  }
  .address {
    position: absolute;
    left: 44px;
    top: 156px;
    font-size: 18px;
    line-height: 1.45;
    letter-spacing: 0.5px;
  }
  .contacts {
    position: absolute;
    left: 44px;
    top: 240px;
    list-style: none;
    font-size: 18px;
    letter-spacing: 0.5px;
  }
  .contacts li {
    display: flex;
    align-items: center;
    gap: 14px;
    height: 34px;
  }
  .contacts svg { width: 20px; height: 20px; flex: none; }

  .back-brand {
    position: absolute;
    right: 36px;
    bottom: 54px;
    font-weight: 700;
    font-size: 30px;
    letter-spacing: 2px;
    text-transform: uppercase;
    line-height: 1.15;
    text-align: center;
    color: var(--emboss);
  }
</style>
</head>
<body>
<main class="canvas">

  <section class="card card--front" aria-label="Card front">
    <div class="front-brand">
      <p class="brand-name">Ridgeline<br>Building Group</p>
    </div>
  </section>

  <section class="card card--back" aria-label="Card back">
    <div class="holder">
      <h1 class="holder-name">Daniel Harper</h1>
      <p class="holder-role">Owner</p>
    </div>

    <address class="address" style="font-style:normal">
      42 Ashcombe Street,<br>Bayview, Vic 3190
    </address>

    <ul class="contacts">
      <li>
        <svg viewBox="0 0 24 24" aria-hidden="true"><path fill="#fff" d="M6.6 10.8a15.1 15.1 0 0 0 6.6 6.6l2.2-2.2a1 1 0 0 1 1-.25 11.4 11.4 0 0 0 3.6.57 1 1 0 0 1 1 1V20a1 1 0 0 1-1 1A17 17 0 0 1 3 4a1 1 0 0 1 1-1h3.5a1 1 0 0 1 1 1c0 1.25.2 2.45.57 3.57a1 1 0 0 1-.25 1z"/></svg>
        <span>0400 555 018</span>
      </li>
      <li>
        <svg viewBox="0 0 24 24" aria-hidden="true"><rect x="2" y="5" width="20" height="14" fill="#fff"/><path d="M2 5l10 8 10-8" fill="none" stroke="#0281ec" stroke-width="1.6"/></svg>
        <span>hello@ridgelinebuild.com</span>
      </li>
      <li>
        <svg viewBox="0 0 24 24" aria-hidden="true"><circle cx="12" cy="12" r="9.5" fill="none" stroke="#fff" stroke-width="2"/><ellipse cx="12" cy="12" rx="4" ry="9.5" fill="none" stroke="#fff" stroke-width="1.6"/><path d="M2.5 12h19" stroke="#fff" stroke-width="1.6"/></svg>
        <span>www.ridgelinebuild.com</span>
      </li>
    </ul>

    <p class="back-brand">Ridgeline<br>Building Group</p>
  </section>

</main>
</body>
</html>
```